business card - Helicopter Flight Services, Flight School, etc.

We need a business card design for a new helicopter service.

We offer Helicopter Flight Services, Aerial Filming & Photography, Flight School, and Helicopter Tours. In that order.

Summit BladeAir, Inc.
Dennis Tollerby
SummitBladeair@Kestmail.com
626-418-7352

Based at the Brenwick Airport in Van Nuys, CA. The final design should communicate integrity and safety. Pictures or logos at your discretion.

Card back side - surprise me.

```html
<!DOCTYPE html>
<html lang="en">
<head>
<meta charset="utf-8">
<title>Summit BladeAir, Inc. – Business Card</title>
<link rel="stylesheet" href="https://fonts.googleapis.com/css2?family=Arimo:wght@400;700&family=Libre+Baskerville:wght@700&display=swap">
<style>
  :root {
    --page-bg: #e9e7e3;
    --card-white: #ffffff;
    --card-black: #050505;
    --brand-blue: #2f6fab;
    --ink: #111111;
    --light-text: #f2f2f2;
    --sky-top: #4f8fd1;
    --sky-mid: #a9d4ee;
    --haze-pink: #8c5f7f;
    --band-white: rgba(255, 255, 255, 0.78);
  }
  * { margin: 0; padding: 0; box-sizing: border-box; }
  html, body {
    width: 1200px;
    height: 902px;
    overflow: hidden;
    background: var(--page-bg);
  }
  .canvas {
    position: relative;
    width: 1200px;
    height: 902px;
  }
  .card {
    position: absolute;
    top: 291px;
    width: 560px;
    height: 320px;
    overflow: hidden;
    box-shadow: 0 6px 18px rgba(0, 0, 0, 0.18);
  }
  .card--back { left: 27px; }
  .card--front { left: 613px; background: var(--card-white); }
  .card svg { display: block; }
  .brand-title {
    font-family: "Libre Baskerville", Georgia, serif;
    font-weight: 700;
  }
  .sans {
    font-family: "Arimo", Arial, sans-serif;
  }
</style>
</head>
<body>
<main class="canvas">

  <section class="card card--back" aria-label="Card back">
    <svg width="560" height="320" viewBox="0 0 560 320">
      <defs>
        <linearGradient id="skyGradient" x1="0" y1="0" x2="0" y2="1">
          <stop offset="0" stop-color="var(--sky-top)"/>
          <stop offset="0.55" stop-color="var(--sky-mid)"/>
          <stop offset="0.85" stop-color="#b9d9ec"/>
          <stop offset="1" stop-color="var(--haze-pink)"/>
        </linearGradient>
      </defs>
      <rect class="hero-photo" width="560" height="320" fill="url(#skyGradient)"
            role="img" aria-label="Helicopter flying through a blue sky above scattered falling roses and pink clouds"/>
      <rect class="name-band" x="0" y="128" width="560" height="80" fill="var(--band-white)"/>
      <text class="brand-title" x="280" y="168" text-anchor="middle" font-size="31" fill="var(--ink)">Summit BladeAir, Inc.</text>
      <text class="sans tagline" x="296" y="194" text-anchor="middle" font-size="17" fill="var(--ink)">Airport · Tour guide · Heliport</text>
    </svg>
  </section>

  <section class="card card--front" aria-label="Card front">
    <svg width="560" height="320" viewBox="0 0 560 320">
      <path class="wave-blue" d="M0,200 C140,232 320,196 560,100 L560,320 L0,320 Z" fill="var(--brand-blue)"/>
      <path class="wave-black" d="M0,214 C140,246 320,210 560,114 L560,320 L0,320 Z" fill="var(--card-black)"/>

      <text class="brand-title" x="145" y="88" font-size="32" fill="var(--brand-blue)">Summit BladeAir, Inc.</text>
      <text class="sans tagline" x="185" y="116" font-size="17" fill="var(--ink)">Airport · Tour guide · Heliport</text>

      <text class="sans person-name" x="22" y="294" font-size="23" fill="var(--light-text)">Dennis Tollerby</text>

      <line class="contact-divider" x1="232" y1="226" x2="232" y2="306" stroke="var(--light-text)" stroke-width="1.5"/>

      <g class="contact-list sans" font-size="12.5" fill="var(--light-text)">
        <rect x="240" y="229" width="13" height="13" rx="1.5" fill="var(--light-text)"/>
        <path d="M243,232 q0,-1 1,-1 h5 q1,0 1,1 l-1,2 h-1 v3 h-4 v-3 h-1 z" fill="var(--card-black)"/>
        <text x="260" y="240">626-418-7352</text>

        <rect x="240" y="248" width="13" height="13" rx="1.5" fill="var(--light-text)"/>
        <text x="260" y="259">Summit BladeAir Inc.</text>

        <rect x="240" y="267" width="13" height="13" rx="1.5" fill="var(--light-text)"/>
        <rect x="242.5" y="270.5" width="8" height="6" fill="none" stroke="var(--card-black)" stroke-width="1"/>
        <path d="M242.5,270.5 L246.5,274 L250.5,270.5" fill="none" stroke="var(--card-black)" stroke-width="1"/>
        <text x="260" y="278">SummitBladeair@Kestmail.com</text>

        <rect x="240" y="286" width="13" height="13" rx="1.5" fill="var(--light-text)"/>
        <path d="M246.5,296.5 C244,293.5 243.5,292.5 243.5,291.5 a3,3 0 0 1 6,0 c0,1 -0.5,2 -3,5 z" fill="var(--card-black)"/>
        <circle cx="246.5" cy="291.5" r="1" fill="var(--light-text)"/>
        <text x="260" y="297" font-size="12">2740 W. Larkspur Ave. Ste.B Halden, CA 91620</text>
      </g>
    </svg>
  </section>

</main>
</body>
</html>
```